Biz Card Design TVCP

New business card for a new company.
Logo was completed by a designer on ArtHarbor and looking to continue requesting additional services.
Company Name: Tidal Vector Power Consulting
Although this company is starting in Canada, we will be moving towards a global presence within the next 6 months.
Key elements to this business are as follows.
Energy Procurement
Energy Reduction Services
Demand Side Consulting
Energy Efficiency Consulting
Saving Clients Money
Helping Them Go "Green"
Managing Their Energy Requirements
Basically the goal for our company is to find the best procurement solution for our clients and reduce their energy consumption. This reduces their expenses and the amount of greenhouse gas they produce on a daily basis.
I have been in the energy footprint for the last 20 years and know that most companies are looking to "do whatever is necessary to get them to sign on the dotted line". I would prefer to walk away from a client that I can't help than to put them into a situation that they will regret for years to come. This is where the "TIDAL" part of the company name comes from.
The following is a catch phrase that encompasses what we do.
"Reducing your carbon footprint & energy bill at the same time!"
The back of the card needs to have this statement along with some sort of illustration. The back is a playground for creative ideas.
The front of the card needs the following.
Logo.
First & Last Name (Gus Marwick)
Title (Energy Warrior)
Phone Number (555) 314-2718
Fax Number (555) 271-8314
Email Address gus@tidalvectorpowerconsulting.example
Address 47 fenwick rd Toronto Ontario K4T 2P9
I want it to be a card that is remembered when any of my staff give it to a customer. It HAS to stand out.
Target Market(s)
Business Owners, Decision Makers, 30 to 65+
Industry/Entity Type
Business
Look and feel

```html
<!DOCTYPE html>
<html lang="en">
<head>
<meta charset="utf-8">
<title>Tidal Vector Power Consulting – Business Card</title>
<link href="https://fonts.googleapis.com/css2?family=Open+Sans:wght@400;600;700&display=swap" rel="stylesheet">
<style>
  :root {
    --page: #e9e6e1;
    --blue-deep: #24498a;
    --blue: #3464b0;
    --blue-light: #4677c2;
    --blue-text: #3a64ae;
    --green: #2e9a44;
    --green-light: #8cc965;
    --white: #ffffff;
    --shadow: rgba(0, 0, 0, 0.25);
  }
  * { box-sizing: border-box; margin: 0; padding: 0; }
  html, body {
    width: 1200px; height: 900px; overflow: hidden;
    background: var(--page);
    font-family: "Open Sans", Arial, sans-serif;
  }
  .card {
    position: absolute; left: 250px; width: 700px; height: 400px;
    overflow: hidden; box-shadow: 0 8px 22px var(--shadow);
  }
  .card--back {
    top: 30px;
    background: linear-gradient(135deg, var(--blue-deep) 0%, var(--blue) 70%, var(--blue-light) 100%);
  }
  .card--front { top: 470px; background: var(--white); }

  /* back */
  .back-decoration {
    position: absolute; left: 0; top: 0; width: 430px; height: 352px;
    background: radial-gradient(ellipse at 55% 45%, rgba(90, 140, 210, 0.45) 0%, rgba(60, 110, 190, 0.2) 45%, rgba(36, 73, 138, 0) 75%);
  }
  .back-logo {
    position: absolute; right: 40px; top: 120px; width: 360px;
    display: flex; flex-direction: column; align-items: flex-end; gap: 14px;
  }
  .back-logo__mark { width: 44px; height: 44px; border-radius: 50%; background: var(--white); }
  .back-logo__name {
    color: var(--white); font-weight: 700; font-size: 28px; line-height: 1.15; text-align: right;
  }
  .back-tagline {
    position: absolute; left: 0; bottom: 0; width: 100%; height: 48px;
    background: var(--blue-light);
    color: var(--white); font-size: 15px; font-weight: 400;
    display: flex; align-items: center; justify-content: center;
  }

  /* front */
  .front-shapes { position: absolute; inset: 0; }
  .front-logo {
    position: absolute; left: 40px; top: 165px;
    display: flex; align-items: center; gap: 14px;
  }
  .front-logo__mark { width: 40px; height: 40px; border-radius: 50%; background: var(--green); flex: none; }
  .front-logo__name { color: var(--blue-text); font-weight: 700; font-size: 27px; line-height: 1.15; }
  .holder {
    position: absolute; right: 262px; top: 34px; text-align: right;
  }
  .holder__name { color: var(--blue-text); font-weight: 700; font-size: 21px; line-height: 1.1; }
  .holder__title { color: var(--blue-text); font-weight: 700; font-size: 12px; }
  .contacts {
    position: absolute; right: 24px; top: 172px;
    list-style: none; text-align: right; color: var(--white);
    font-size: 12px; line-height: 26px;
  }
  .contacts li { display: flex; align-items: center; justify-content: flex-end; gap: 6px; white-space: nowrap; }
  .contacts svg { width: 11px; height: 11px; fill: var(--white); flex: none; }
  .front-tagline {
    position: absolute; right: 22px; bottom: 22px;
    color: var(--white); font-size: 11px; white-space: nowrap;
  }
</style>
</head>
<body>

<section class="card card--back" aria-label="Business card back">
  <div class="back-decoration" role="img" aria-label="Faint large leaf and lightning bolt decoration"></div>
  <div class="back-logo">
    <span class="back-logo__mark"></span>
    <span class="back-logo__name">Tidal Vector<br>Power Consulting</span>
  </div>
  <p class="back-tagline">"Reducing your carbon footprint &amp; energy bill at the same time!"</p>
</section>

<section class="card card--front" aria-label="Business card front">
  <svg class="front-shapes" viewBox="0 0 700 400" aria-hidden="true">
    <defs>
      <linearGradient id="swoosh" x1="0" y1="0" x2="0" y2="1">
        <stop offset="0" stop-color="#8cc965"/>
        <stop offset="1" stop-color="#2e9a44"/>
      </linearGradient>
      <linearGradient id="panel" x1="0" y1="0" x2="1" y2="1">
        <stop offset="0" stop-color="#3a6ab6"/>
        <stop offset="1" stop-color="#2f5ca6"/>
      </linearGradient>
    </defs>
    <path d="M483,0 C423,130 343,265 228,400 L270,400 C353,268 430,128 488,0 Z" fill="url(#swoosh)"/>
    <path d="M500,0 C440,130 370,270 280,400 L700,400 L700,0 Z" fill="url(#panel)"/>
  </svg>

  <div class="front-logo">
    <span class="front-logo__mark"></span>
    <span class="front-logo__name">Tidal Vector<br>Power Consulting</span>
  </div>

  <div class="holder">
    <p class="holder__name">Gus Marwick</p>
    <p class="holder__title">Energy Warrior</p>
  </div>

  <ul class="contacts">
    <li>(555) 314-2718
      <svg viewBox="0 0 12 12"><path d="M2.5 1 L4.5 1 L5.5 3.5 L4.2 4.5 C4.8 5.9 6.1 7.2 7.5 7.8 L8.5 6.5 L11 7.5 L11 9.5 C11 10.3 10.3 11 9.5 11 C5 11 1 7 1 2.5 C1 1.7 1.7 1 2.5 1 Z"/></svg>
    </li>
    <li>(555) 271-8314
      <svg viewBox="0 0 12 12"><path d="M1 3 H11 V10 H1 Z M3 1 H9 V3 H3 Z"/><rect x="3" y="5" width="6" height="1.2" fill="#3464b0"/><rect x="3" y="7.2" width="6" height="1.2" fill="#3464b0"/></svg>
    </li>
    <li>gus@tidalvectorpowerconsulting.example
      <svg viewBox="0 0 12 12"><path d="M1 2.5 H11 V9.5 H1 Z"/><path d="M1 2.5 L6 6.5 L11 2.5" stroke="#3464b0" stroke-width="1" fill="none"/></svg>
    </li>
    <li>47 fenwick rd Toronto Ontario K4T 2P9
      <svg viewBox="0 0 12 12"><path d="M6 1 L11 6 H9.5 V11 H7 V8 H5 V11 H2.5 V6 H1 Z"/></svg>
    </li>
  </ul>

  <p class="front-tagline">"Reducing your carbon footprint &amp; energy bill at the same time!"</p>
</section>

</body>
</html>
```